Stationery Design Project

We need a stationery design for our Norwegian trucking company. We have existed for about 15 years and our 12 drivers uses relatively new vehicles to transport goods around in northern Norway. Long distance routes with fresh fish og food transport is our main operations.

We have already made alogo that's printed on our trucks. The logo and a picture of our trucks is attached. I think the logo i crappy, but since its already in use, changing it is not an option in this round. Still using a better colour scheme in the overall stationery and more interesting fonts is possible (altso in the logo).

Company details:
Name: Kjelvraket AS
Organisation nr 873 615 309
Post adress: 8642 Raudvik

I like minimalism and simplicity. I am avalibly for questions in normal GMT working hours either here or on mail: ivar@fjordlast.no

Reason: Hi. Im extending the deadline because I needed some time to find a vector file of our logo. Sorry for the inconvenience

Hi, and thanks for all your interest in the project. Some updates:

-          I have decided to commit to using one of the designs. Some designer will get the payment.

-          I have extended the deadline with 24 hours since I needed some time to find our firms vector logo (a slow Swedish man was holding me up)

-          We will not choose a design before the deadline. No need to rush.

-          We have received a lot of great design and think there is a need to specified the product we want to make:

o   Business Card for all our employers. I just need the design and will duplicate with the correct numbers and name myself. The information on should be: Logo, employer’s name, Phone number, email, website, Postal number and address. Use this as a template: logo, Leif Brattvoll, 47382066, Leif@fjordlast.no,, fjordlast.no, 8642 Raudvik. The order and placement of the information is your creative decision.

o   Stickers to put on the goods we travel. On the sticker the should be the following information: Logo, phone number, Tekst and link: Fraktæ av Kjelvraket. Ke du syns? Fjordlast.no/tilbakemelding (this means: Handled by Kjelvraket. What do you think Fjordlast.no/feedback -à the link will be a feedback form). The placement the information and size is your creative decision with some stings: we have been thinking of using Drukko for printing and see that a size about 6x6 cm, 8x5 or something like that. (with 3000 copies our budget is 200 punds). Any suggestions of other suppliers are welcome. Drukko price calculator http://www.drukkolabelhouse.co.uk/digital-litho-printing/printing-labels-tags/stickers/

o   Letterhead with logo, address, phone number and organizational number.

o   Envelopes with logo,address, phone number and organizational number.

Have a nice day.

 

 

• Using the blue colour in the logo and using a similar graphic approch.

```html
<!DOCTYPE html>
<html lang="no">
<head>
<meta charset="utf-8">
<title>Kjelvraket AS – Stationery</title>
<link href="https://fonts.googleapis.com/css2?family=Roboto:wght@400;700&display=swap" rel="stylesheet">
<style>
:root{
  --bg:#9b9ea0;
  --paper:#ffffff;
  --blue-deep:#0b4ea3;
  --blue-bright:#1b7cc3;
  --ink:#2b2b2b;
  --muted:#6a6a6a;
  --rule:#b9b9b9;
  --ghost:#eef1f7;
}
*{box-sizing:border-box;margin:0;padding:0}
html,body{width:1200px;height:941px;overflow:hidden}
body{background:var(--bg);font-family:"Roboto",Arial,sans-serif;color:var(--ink);position:relative}
.sheet{position:absolute;background:var(--paper);box-shadow:0 0 0 1px #7c7f81}
.wordmark{font-family:"Roboto",Arial,sans-serif;font-weight:700;color:var(--blue-deep);letter-spacing:.2px;white-space:nowrap}
.wordmark.on-dark{color:#fff}
.mark-dot{display:inline-block;width:.55em;height:.55em;border-radius:50%;background:currentColor;margin-right:.3em;vertical-align:.08em}
.contact{font-size:7px;line-height:9.5px;color:var(--ink)}
.contact .org{color:var(--blue-bright)}
.contact .ico{display:inline-block;width:5px;height:5px;border-radius:50%;background:#444;margin-right:3px;vertical-align:0}

/* business cards */
.card{width:216px;height:122px}
.card .wordmark{position:absolute;left:22px;top:50px;font-size:16px}
.card .divider{position:absolute;left:125px;top:26px;width:2px;height:72px;background:var(--blue-bright)}
.card .person{position:absolute;left:133px;top:26px;font-size:10px;font-weight:700;color:var(--blue-bright)}
.card .contact{position:absolute;left:133px;top:43px}
.card .contact .post{margin-top:5px}
.card-logo .wordmark{left:0;right:0;top:42px;text-align:center;font-size:23px}
.card-logo .url{position:absolute;left:0;right:0;bottom:14px;text-align:center;font-size:8px;letter-spacing:2px;color:#333}
.card-blue{background:var(--blue-deep);box-shadow:none}
.card-blue.bright{background:var(--blue-bright)}
.card-blue .wordmark{left:0;right:0;top:40px;text-align:center;font-size:23px}
.card-blue .url{position:absolute;left:0;right:0;bottom:12px;text-align:center;font-size:8px;letter-spacing:2px;color:#fff}

/* stickers */
.sticker-round{position:absolute;width:98px;height:98px;border-radius:50%;background:#fff;border:4px dotted var(--blue-deep);text-align:center;font-family:Georgia,serif;font-size:5px;line-height:6px;color:var(--ink);padding-top:20px}
.sticker-round .wordmark{font-size:9px;margin:3px 0;font-family:"Roboto",Arial,sans-serif}
.sticker-round .phone{font-size:7px;color:var(--blue-deep)}
.sticker-star{position:absolute;width:100px;height:100px}
.sticker-star .txt{position:absolute;inset:0;text-align:center;font-family:Georgia,serif;font-size:5px;line-height:6px;color:#fff;padding-top:24px}
.sticker-star .wordmark{font-size:9px;margin:3px 0;font-family:"Roboto",Arial,sans-serif}
.sticker-star .phone{font-size:7px}
.sticker-tag{position:absolute;left:1000px;top:86px;width:130px;height:80px;border-radius:7px;background:var(--blue-deep);color:#fff}
.sticker-tag .bubble{position:absolute;left:10px;top:8px;width:68px;height:34px;border:3px solid #5fa0dc;border-radius:50%;display:flex;align-items:center;justify-content:center}
.sticker-tag .wordmark{font-size:8px}
.sticker-tag .msg{position:absolute;left:10px;top:49px;font-family:Georgia,serif;font-size:5.5px;line-height:6.5px}
.sticker-tag .phone{position:absolute;right:4px;top:40px;transform:translateY(-50%) rotate(90deg);font-family:Georgia,serif;font-size:11px;letter-spacing:.5px}

/* compliment slip */
.slip{left:214px;top:206px;width:390px;height:174px}
.slip .wordmark{position:absolute;left:16px;top:24px;font-size:22px}
.slip .place{position:absolute;left:17px;top:55px;font-size:7px;letter-spacing:2px;color:#444}
.slip .contact{position:absolute;left:17px;top:68px}

/* envelope */
.envelope{left:67px;top:383px;width:390px;height:249px}
.envelope svg{position:absolute;left:0;top:0}
.envelope .flap-name{position:absolute;font-size:17px}

/* letterhead */
.letter{left:414px;top:414px;width:349px;height:451px}
.letter .wordmark{position:absolute;left:0;right:0;top:24px;text-align:center;font-size:22px}
.letter .place{position:absolute;left:284px;top:32px;font-size:7px;color:#333;border-left:1px solid #999;padding-left:3px}
.letter .ghost{position:absolute;left:0;right:0;top:182px;text-align:center;font-size:44px;color:var(--ghost)}
.letter .foot{position:absolute;left:0;right:0;bottom:4px;text-align:center;font-size:6.5px}

/* fax */
.fax{left:777px;top:414px;width:349px;height:451px}
.fax .wordmark{position:absolute;left:104px;top:24px;font-size:22px}
.fax .contact{position:absolute;left:279px;top:18px;border-left:2px solid var(--blue-bright);padding-left:5px}
.fax h1{position:absolute;left:29px;top:101px;font-size:20px;font-weight:700;color:#111}
.fax .fields{position:absolute;left:29px;top:150px;width:300px}
.fax .row{display:flex;gap:20px;margin-bottom:10px}
.fax .field{flex:1;display:flex;font-size:5.5px;font-weight:700;font-style:normal;border-bottom:1px solid var(--rule);padding-bottom:1px}
.fax .field.wide{flex:1.7}
.fax .checks{position:absolute;left:29px;top:239px;width:305px;display:flex;justify-content:space-between;font-size:6px;color:#333}
.fax .checks span::before{content:"";display:inline-block;width:6px;height:6px;background:#ddd;margin-right:4px;vertical-align:-1px}
.fax .foot{position:absolute;left:0;right:0;bottom:4px;text-align:center;font-size:6.5px;letter-spacing:1.5px;color:#444}
</style>
</head>
<body>

<!-- business card, front -->
<div class="sheet card" style="left:267px;top:57px">
  <div class="wordmark">Kjelvraket</div>
  <div class="divider"></div>
  <div class="person">Leif Brattvoll</div>
  <div class="contact">
    <div><span class="ico"></span>47382066</div>
    <div class="org">Org nr <span style="color:var(--ink)">873 615 309</span></div>
    <div><span class="ico"></span>Leif@fjordlast.no</div>
    <div><span class="ico"></span>www.fjordlast.no</div>
    <div class="post"><span class="ico"></span>8642 Raudvik</div>
  </div>
</div>

<!-- business card, back -->
<div class="sheet card card-logo" style="left:512px;top:57px">
  <div class="wordmark"><span class="mark-dot"></span>Kjelvraket</div>
  <div class="url">www.fjordlast.no</div>
</div>

<!-- round sticker -->
<div class="sticker-round" style="left:771px;top:73px">
  Tekst and link:<br>Fraktæ av Kjelvraket.<br>Ke du syns?<br>Fjordlast.no/tilbakemelding
  <div class="wordmark">Kjelvraket</div>
  <div class="phone">47-382-066</div>
</div>

<!-- star sticker -->
<div class="sticker-star" style="left:882px;top:73px">
  <svg width="100" height="100" viewBox="0 0 100 100" aria-hidden="true">
    <polygon fill="var(--blue-deep)" points="50,2 56,10 65,4 68,14 78,11 78,21 89,22 85,31 95,36 88,44 97,50 88,56 95,64 85,69 89,78 78,79 78,89 68,86 65,96 56,90 50,98 44,90 35,96 32,86 22,89 22,79 11,78 15,69 5,64 12,56 3,50 12,44 5,36 15,31 11,22 22,21 22,11 32,14 35,4 44,10"/>
    <circle cx="50" cy="50" r="38" fill="none" stroke="#5fa0dc" stroke-width="1"/>
  </svg>
  <div class="txt">
    <div class="wordmark on-dark">Kjelvraket</div>
    Tekst and link:<br>Fraktæ av Kjelvraket.<br>Ke du syns?<br>Fjordlast.no/tilbakemelding
    <div class="phone">47-382-066</div>
  </div>
</div>

<!-- rectangular sticker -->
<div class="sticker-tag">
  <div class="bubble"><span class="wordmark on-dark">Kjelvraket</span></div>
  <div class="msg">Tekst and link:<br>Fraktæ av Kjelvraket. Ke du syns?<br>Fjordlast.no/tilbakemelding</div>
  <div class="phone">47-382-066</div>
</div>

<!-- compliment slip -->
<div class="sheet slip">
  <div class="wordmark"><span class="mark-dot"></span>Kjelvraket</div>
  <div class="place">8642 Raudvik</div>
  <div class="contact">
    <div><span class="ico"></span>47382066</div>
    <div class="org">Org nr <span style="color:var(--ink)">873 615 309</span></div>
    <div><span class="ico"></span>www.fjordlast.no</div>
  </div>
</div>

<!-- blue cards -->
<div class="sheet card card-blue" style="left:637px;top:233px">
  <div class="wordmark on-dark"><span class="mark-dot"></span>Kjelvraket</div>
  <div class="url">www.fjordlast.no</div>
</div>
<div class="sheet card card-blue bright" style="left:870px;top:233px">
  <div class="wordmark on-dark"><span class="mark-dot"></span>Kjelvraket</div>
  <div class="url">www.fjordlast.no</div>
</div>

<!-- envelope -->
<div class="sheet envelope">
  <svg width="390" height="249" viewBox="0 0 390 249" aria-hidden="true">
    <path d="M0 0 H390 V10 L340 58 Q200 78 0 58 Z" fill="var(--blue-bright)"/>
    <path d="M0 74 H390 V84 L340 130 Q200 150 0 130 Z" fill="var(--blue-deep)"/>
  </svg>
  <div class="wordmark on-dark flap-name" style="left:170px;top:22px">Kjelvraket</div>
  <div class="wordmark on-dark flap-name" style="left:165px;top:96px">Kjelvraket</div>
</div>

<!-- small business card -->
<div class="sheet card" style="left:126px;top:669px">
  <div class="wordmark">Kjelvraket</div>
  <div class="divider"></div>
  <div class="person">Leif Brattvoll</div>
  <div class="contact">
    <div><span class="ico"></span>47382066</div>
    <div class="org">Org nr <span style="color:var(--ink)">873 615 309</span></div>
    <div><span class="ico"></span>Leif@fjordlast.no</div>
    <div><span class="ico"></span>www.fjordlast.no</div>
    <div class="post"><span class="ico"></span>8642 Raudvik</div>
  </div>
</div>

<!-- letterhead -->
<div class="sheet letter">
  <div class="wordmark"><span class="mark-dot"></span>Kjelvraket</div>
  <div class="place">8642 Raudvik</div>
  <div class="wordmark ghost">Kjelvraket</div>
  <div class="foot contact">47382066 &nbsp;<span class="org">Org nr</span> 873 615 309 &nbsp; www.fjordlast.no</div>
</div>

<!-- fax -->
<div class="sheet fax">
  <div class="wordmark"><span class="mark-dot"></span>Kjelvraket</div>
  <div class="contact">
    <div class="org">Org nr <span style="color:var(--ink)">873 615 309</span></div>
    <div><span class="ico"></span>47382066</div>
    <div><span class="ico"></span>www.fjordlast.no</div>
  </div>
  <h1>FAX</h1>
  <div class="fields">
    <div class="row"><div class="field wide">To :</div><div class="field">From :</div></div>
    <div class="row"><div class="field wide">Fax :</div><div class="field">Pages :</div></div>
    <div class="row"><div class="field wide">Phone :</div><div class="field">Date :</div></div>
    <div class="row"><div class="field wide">Re :</div><div class="field">CC :</div></div>
  </div>
  <div class="checks">
    <span>Urgent</span><span>For Review</span><span>Please Comment</span><span>Please Reply</span><span>Please Recycle</span>
  </div>
  <div class="foot">8642 Raudvik</div>
</div>

</body>
</html>
```